Harborline Auto LLC

Car Dealer Customer Service
Address: 2874 Cresthaven Road, Shelbyville, TN 37162
web: www.harborlineautoxq.net
email: harborlineautoxq@mailnest.example
Phone: (931) 555-0148
Phone: (629) 555-0173

```html
<!DOCTYPE html>
<html lang="en">
<head>
<meta charset="utf-8">
<title>Harborline Auto – Business Card</title>
<link rel="stylesheet" href="https://fonts.googleapis.com/css2?family=Montserrat:wght@600;800&family=Arimo:wght@400&display=swap">
<style>
  :root {
    --bg: #c9c9c9;
    --blue: #1f86c1;
    --blue-deep: #1a74a9;
    --orange: #f0ad3b;
    --white: #ffffff;
    --ink: #2b2b2b;
    --muted-gray: #f1f1f1;
  }
  * { margin: 0; padding: 0; box-sizing: border-box; }
  html, body { width: 1200px; height: 900px; overflow: hidden; }
  body {
    background: var(--bg);
    font-family: "Arimo", Arial, sans-serif;
    position: relative;
  }
  .card {
    position: absolute;
    left: 290px;
    width: 620px;
    height: 354px;
    border-radius: 22px;
    box-shadow: 0 6px 14px rgba(0,0,0,0.25);
    overflow: hidden;
  }
  .card-front {
    top: 76px;
    background: linear-gradient(160deg, var(--blue) 0%, var(--blue-deep) 100%);
    display: flex;
    flex-direction: column;
    align-items: center;
    justify-content: center;
    gap: 14px;
  }
  .card-back { top: 470px; background: var(--white); }

  .brand {
    display: flex;
    align-items: center;
    gap: 16px;
    font-family: "Montserrat", sans-serif;
    font-weight: 800;
    text-transform: uppercase;
    letter-spacing: 1px;
  }
  .brand-dot { border-radius: 50%; flex: none; }
  .card-front .brand { color: var(--white); font-size: 42px; }
  .card-front .brand-dot { width: 54px; height: 54px; background: var(--orange); }
  .tagline {
    font-family: "Montserrat", sans-serif;
    font-weight: 800;
    color: var(--orange);
    font-size: 17px;
    letter-spacing: 3px;
    text-transform: uppercase;
  }

  .back-left { position: absolute; left: 44px; top: 44px; }
  .card-back .brand { color: var(--blue); font-size: 30px; gap: 12px; }
  .card-back .brand-dot { width: 38px; height: 38px; background: var(--orange); }
  .person-name {
    margin-top: 44px;
    font-family: "Montserrat", sans-serif;
    font-weight: 800;
    color: var(--blue);
    font-size: 22px;
    text-transform: uppercase;
  }
  .person-role { color: var(--orange); font-size: 19px; margin-top: 2px; }
  .contact-list { list-style: none; margin-top: 16px; color: var(--ink); font-size: 18px; }
  .contact-list li { display: flex; align-items: center; gap: 10px; line-height: 28px; }
  .contact-list svg { width: 18px; height: 18px; fill: var(--blue); flex: none; }

  .back-right {
    position: absolute;
    right: 40px;
    top: 96px;
    text-align: right;
    color: var(--ink);
    font-size: 18px;
    line-height: 27px;
  }
  .web-url { margin-bottom: 8px; }
  .web-url .domain { color: var(--blue); }
</style>
</head>
<body>

  <section class="card card-front">
    <div class="brand"><span class="brand-dot"></span>Harborline Auto</div>
    <div class="tagline">Car Dealer Customer Service</div>
  </section>

  <section class="card card-back">
    <div class="back-left">
      <div class="brand"><span class="brand-dot"></span>Harborline Auto</div>
      <div class="person-name">Marcus Delaney</div>
      <div class="person-role">Managing Director</div>
      <ul class="contact-list">
        <li>
          <svg viewBox="0 0 24 24" aria-hidden="true"><path d="M6.6 10.8a15.1 15.1 0 0 0 6.6 6.6l2.2-2.2a1 1 0 0 1 1-.25 11.4 11.4 0 0 0 3.6.57 1 1 0 0 1 1 1V20a1 1 0 0 1-1 1A17 17 0 0 1 3 4a1 1 0 0 1 1-1h3.5a1 1 0 0 1 1 1c0 1.25.2 2.45.57 3.57a1 1 0 0 1-.25 1z"/></svg>
          (931) 555-0148
        </li>
        <li>
          <svg viewBox="0 0 24 24" aria-hidden="true"><path d="M6.6 10.8a15.1 15.1 0 0 0 6.6 6.6l2.2-2.2a1 1 0 0 1 1-.25 11.4 11.4 0 0 0 3.6.57 1 1 0 0 1 1 1V20a1 1 0 0 1-1 1A17 17 0 0 1 3 4a1 1 0 0 1 1-1h3.5a1 1 0 0 1 1 1c0 1.25.2 2.45.57 3.57a1 1 0 0 1-.25 1z"/></svg>
          (629) 555-0173
        </li>
        <li>
          <svg viewBox="0 0 24 24" aria-hidden="true"><path d="M2 5h20v14H2z M2 5l10 8 10-8" fill="none" stroke="#1f86c1" stroke-width="2"/></svg>
          harborlineautoxq@mailnest.example
        </li>
      </ul>
    </div>

    <div class="back-right">
      <div class="web-url">www.<span class="domain">harborlineautoxq</span>.net</div>
      <div class="address">2874 Cresthaven Road<br>Shelbyville, TN 37162</div>
    </div>
  </section>

</body>
</html>
```